Print materials for 3-star hotel

We are changing up our print materials (notepads, letterheads, key card jackets, small flyer for the room rates) We are a 3 star business hotel in the Philippines and have mainly used grey tones and clean, simple lines. See attached photos for logo and hotel interior photos.

Target Market(s)

Business

Contact Information for Business Card

Corvale Terrace Hotel
Lindwell Banca Avenue corner Tolenta St Cebu City 6000 Philippines
Tel: +63 32 481 7302
Mobile: +63 917 648 2095
www.corvaleterracehotel.example

Font styles to use
Serif
Sans Serif

Requirements
Must have
• Simple
• Readable font and font size
Nice to have
• Neutral colors, grey and taupes
Should not have
• No purples and bright blues

```html
<!DOCTYPE html>
<html lang="en">
<head>
<meta charset="utf-8">
<title>Corvale Terrace Hotel — Stationery</title>
<link rel="stylesheet" href="https://fonts.googleapis.com/css2?family=Montserrat:wght@400;500;600;700&display=swap">
<style>
:root{
  --backdrop:#b4b4b4;
  --paper:#ececec;
  --paper-light:#f2f2f2;
  --slate:#7b7b7b;
  --slate-dark:#6c6c6c;
  --band:#5a5a5a;
  --flap:#7d7d7d;
  --ink:#6a6a6a;
  --ink-soft:#8a8a8a;
  --signature:#dcdcdc;
  --white:#f4f4f4;
}
*{box-sizing:border-box;margin:0;padding:0}
html,body{width:1200px;height:1150px;overflow:hidden}
body{background:var(--backdrop);font-family:"Montserrat",Arial,sans-serif;color:var(--ink);position:relative}
address{font-style:normal}
.piece{position:absolute}
.sheet-backing{left:97px;top:211px;width:468px;height:662px;background:var(--slate)}
.letterhead{left:38px;top:133px;width:470px;height:662px;background:var(--paper)}
.brand{display:flex;align-items:center;gap:8px;font-weight:500;letter-spacing:2px;text-transform:uppercase;color:var(--ink);white-space:nowrap}
.brand-mark{width:10px;height:10px;background:currentColor;flex:none}
.letterhead .brand{position:absolute;left:42px;top:62px;font-size:12px}
.contact{font-size:7px;line-height:10.5px;color:var(--ink)}
.contact b{font-weight:700}
.letterhead .contact{position:absolute;right:42px;top:36px;text-align:right}
.phones{margin-top:8px}
.phone{display:flex;align-items:center;gap:4px;white-space:nowrap}
.letterhead .phone{justify-content:flex-end}
.phone svg{width:7px;height:7px;flex:none}
.letter-body{position:absolute;left:42px;right:42px;top:190px;font-size:6.4px;line-height:14px;color:var(--ink-soft);text-align:justify}
.letter-body p{margin-bottom:14px}
.letter-body .sender{font-weight:700;color:var(--ink)}
.signature{width:124px;height:18px;background:var(--signature);margin-top:6px}
.letter-footer{position:absolute;left:0;right:0;bottom:24px;text-align:center;font-size:8px;font-weight:600;color:var(--ink);white-space:nowrap}
.letter-footer span{margin:0 10px}
.envelope-back{left:605px;top:126px;width:465px;height:230px;background:var(--paper)}
.envelope-back svg{position:absolute;left:0;top:0}
.envelope-back .brand{position:absolute;left:0;right:0;top:148px;justify-content:center;font-size:11px}
.envelope-front{left:709px;top:397px;width:466px;height:232px;background:var(--paper-light)}
.envelope-front .contact{position:absolute;left:27px;top:146px}
.envelope-front .web{position:absolute;right:26px;bottom:22px;text-align:right;font-size:7px;line-height:10.5px}
.card{top:901px;width:244px;height:135px}
.card-front{left:211px;background:var(--paper-light);padding:24px 19px}
.card-name{font-size:9px;font-weight:700;color:var(--ink)}
.card-role{font-size:5.5px;margin-top:2px}
.card-rule{width:18px;height:1px;background:var(--ink-soft);margin:15px 0 14px}
.card-front .contact{font-size:5.6px;line-height:9px}
.card-front .brand-mark{position:absolute;right:24px;top:24px;width:14px;height:14px;background:var(--ink)}
.card-front .address{position:absolute;right:19px;top:84px;text-align:right;font-size:5.6px;line-height:9px}
.card-back{left:477px;background:var(--slate)}
.card-back .brand{position:absolute;inset:0;justify-content:center;color:var(--white);font-size:10px}
.notebook{left:758px;top:680px;width:270px;height:422px;background:var(--slate-dark);border-radius:4px 14px 14px 4px}
.notebook .band{position:absolute;left:206px;top:0;width:6px;height:100%;background:var(--band)}
.notebook .brand{position:absolute;left:0;width:206px;top:208px;justify-content:center;color:var(--white);font-size:8px;letter-spacing:1.5px;gap:6px}
.notebook .brand-mark{width:8px;height:8px}
</style>
</head>
<body>

<div class="piece sheet-backing" role="img" aria-label="Grey second sheet with a subtle wave pattern"></div>

<article class="piece letterhead">
  <div class="brand"><span class="brand-mark"></span>Corvale Terrace Hotel</div>
  <address class="contact">
    Lindwell Banca Avenue corner<br>Tolenta St, Marivel City<br>Orsena, 4417, <b>Veranda Isles</b>
    <div class="phones">
      <div class="phone">+00 55 481 7302 <svg viewBox="0 0 10 10"><circle cx="5" cy="5" r="4.4" fill="none" stroke="currentColor" stroke-width=".8"/><path d="M3.4 2.8l1 1-.5.6c.3.7.8 1.2 1.5 1.5l.6-.5 1 1-.7.8C4.6 7 3 5.4 2.8 3.5z" fill="currentColor"/></svg></div>
      <div class="phone">+00 871 648 2095 <svg viewBox="0 0 10 10"><circle cx="5" cy="5" r="4.4" fill="none" stroke="currentColor" stroke-width=".8"/><path d="M3.4 2.8l1 1-.5.6c.3.7.8 1.2 1.5 1.5l.6-.5 1 1-.7.8C4.6 7 3 5.4 2.8 3.5z" fill="currentColor"/></svg></div>
      <div class="phone">+00 872 204 5519 <svg viewBox="0 0 10 10"><circle cx="5" cy="5" r="4.4" fill="none" stroke="currentColor" stroke-width=".8"/><path d="M3.4 2.8l1 1-.5.6c.3.7.8 1.2 1.5 1.5l.6-.5 1 1-.7.8C4.6 7 3 5.4 2.8 3.5z" fill="currentColor"/></svg></div>
    </div>
  </address>
  <div class="letter-body">
    <p>Dear Friend,</p>
    <p>Lorem ipsum dolor sit amet, consectetur adipisicing elit, sed do eiusmod tempor incididunt ut labore et dolore magna aliqua. Ut enim ad minim veniam, quis nostrud exercitation ullamco laboris nisi ut aliquip ex ea commodo consequat. Duis aute irure dolor in reprehenderit in voluptate vel nulla pariatur. Excepted est laborum.</p>
    <p>Lorem ipsum dolor sit amet, consectetur adipisicing elit, sed do eiusmod tempor incididunt ut labore et dolore magna aliqua. Ut enim ad minim veniam, quis nostrud exercitation ullamco laboris nisi ut aliquip ex ea commodo consequat. Duis t anim id est laborum. Lorem ipsum dolor sit amet, consectetur adipismodo consequat.</p>
    <p>Excepteur sint occaecat cupidatat non proident, sunt in culpa qui officia deserunt mollit anim id est laborum. Lorem ipsum dolor sit amet, consectetur adipisicing elit, sed do eiusmod oris nisi ut aliquip ex ea commodo consequat. Duis aute irure dolor in reprehenderit in voluptate velit esse cillum dolore eu fugiat nulla pari.</p>
    <p>Lorem ipsum dolor sit amet, consectetur adipisicing elit, sed do eiusmod tempor incididunt ut labore et dolore magna aliqua. Ut enim adonseqquat. Duis aute irure dolor in reprehenderit in voluptate velit esse cillum dolore eu fugiat nulla pariatur.</p>
    <p>Best regards,</p>
    <p class="sender">Adrian Velasco</p>
    <div class="signature" role="img" aria-label="Handwritten signature"></div>
  </div>
  <div class="letter-footer"><span>reservations@corvaleterracehotel.example</span>|<span>www.corvaleterracehotel.example</span></div>
</article>

<section class="piece envelope-back">
  <svg width="465" height="230" viewBox="0 0 465 230" role="img" aria-label="Envelope flap with a subtle wave pattern">
    <path d="M0 0H465V12Q465 34 440 50H25Q0 34 0 12Z" fill="var(--flap)"/>
  </svg>
  <div class="brand"><span class="brand-mark"></span>Corvale Terrace Hotel</div>
</section>

<section class="piece envelope-front">
  <address class="contact">
    Lindwell Banca Avenue corner<br>Tolenta St, Marivel City<br>Orsena, 4417, <b>Veranda Isles</b>
    <div class="phones">
      <div class="phone"><svg viewBox="0 0 10 10"><circle cx="5" cy="5" r="4.4" fill="none" stroke="currentColor" stroke-width=".8"/><path d="M3.4 2.8l1 1-.5.6c.3.7.8 1.2 1.5 1.5l.6-.5 1 1-.7.8C4.6 7 3 5.4 2.8 3.5z" fill="currentColor"/></svg>+00 55 481 7302</div>
      <div class="phone"><svg viewBox="0 0 10 10"><circle cx="5" cy="5" r="4.4" fill="none" stroke="currentColor" stroke-width=".8"/><path d="M3.4 2.8l1 1-.5.6c.3.7.8 1.2 1.5 1.5l.6-.5 1 1-.7.8C4.6 7 3 5.4 2.8 3.5z" fill="currentColor"/></svg>+00 871 648 2095</div>
      <div class="phone"><svg viewBox="0 0 10 10"><circle cx="5" cy="5" r="4.4" fill="none" stroke="currentColor" stroke-width=".8"/><path d="M3.4 2.8l1 1-.5.6c.3.7.8 1.2 1.5 1.5l.6-.5 1 1-.7.8C4.6 7 3 5.4 2.8 3.5z" fill="currentColor"/></svg>+00 872 204 5519</div>
    </div>
  </address>
  <div class="web">reservations@corvaleterracehotel.example<br>www.corvaleterracehotel.example</div>
</section>

<section class="piece card card-front">
  <div class="card-name">Adrian VELASCO</div>
  <div class="card-role">Managing Director</div>
  <div class="card-rule"></div>
  <div class="contact">
    <div class="phone"><svg viewBox="0 0 10 10"><circle cx="5" cy="5" r="4.4" fill="none" stroke="currentColor" stroke-width=".8"/><path d="M3.4 2.8l1 1-.5.6c.3.7.8 1.2 1.5 1.5l.6-.5 1 1-.7.8C4.6 7 3 5.4 2.8 3.5z" fill="currentColor"/></svg>+00 55 481 7302</div>
    <div class="phone"><svg viewBox="0 0 10 10"><circle cx="5" cy="5" r="4.4" fill="none" stroke="currentColor" stroke-width=".8"/><path d="M3.4 2.8l1 1-.5.6c.3.7.8 1.2 1.5 1.5l.6-.5 1 1-.7.8C4.6 7 3 5.4 2.8 3.5z" fill="currentColor"/></svg>+00 871 648 2095</div>
    <div class="phone"><svg viewBox="0 0 10 10"><circle cx="5" cy="5" r="4.4" fill="none" stroke="currentColor" stroke-width=".8"/><path d="M3.4 2.8l1 1-.5.6c.3.7.8 1.2 1.5 1.5l.6-.5 1 1-.7.8C4.6 7 3 5.4 2.8 3.5z" fill="currentColor"/></svg>+00 872 204 5519</div>
    <div class="phone"><svg viewBox="0 0 10 10"><circle cx="5" cy="5" r="4.4" fill="currentColor"/></svg>adrian@corvaleterracehotel.example</div>
    <div class="phone"><svg viewBox="0 0 10 10"><circle cx="5" cy="5" r="4.4" fill="currentColor"/></svg>www.corvaleterracehotel.example</div>
  </div>
  <span class="brand-mark"></span>
  <address class="contact address">Lindwell Banca<br>Avenue corner<br>Tolenta St, Marivel City<br>Orsena, 4417, <b>Veranda Isles</b></address>
</section>

<section class="piece card card-back" role="img" aria-label="Business card back with a subtle wave pattern">
  <div class="brand"><span class="brand-mark"></span>Corvale Terrace Hotel</div>
</section>

<section class="piece notebook">
  <div class="brand"><span class="brand-mark"></span>Corvale Terrace Hotel</div>
  <div class="band"></div>
</section>

</body>
</html>
```